Create a cover for English Grammar Workbook

This book describes a system to learn English in a proper way - we call it The ''Lantern Row'' System.

It focuses on not only teaching grammar and its structures, but also giving students tips on how to use it and the best ways to remember what they learn.

The cover should have 3 realistic pillars (3D), with one closer to the front to show that this book is the 1st (front) Pillar.

The title is: "Building Sentences That Stick: *A Friendly Path Through Usage"*

Author's name: Doreen Calloway

```html
<!DOCTYPE html>
<html lang="en">
<head>
<meta charset="utf-8">
<title>Building Sentences That Stick — Book Cover</title>
<link rel="stylesheet" href="https://fonts.googleapis.com/css2?family=Oswald:wght@400;500&family=Montserrat:wght@500;600&display=swap">
<style>
  :root {
    --backdrop: #0d0d0d;
    --paper: #f7f7f7;
    --ink: #2f2f2f;
    --title-panel: #3b3b3d;
    --accent-red: #c4161c;
    --white: #ffffff;
    --stone-light: #f1f1f1;
    --stone-mid: #d2d2d2;
    --stone-dark: #a8a8a8;
  }
  * { box-sizing: border-box; margin: 0; padding: 0; }
  html, body {
    width: 1200px;
    height: 843px;
    overflow: hidden;
    background: var(--backdrop);
  }
  .canvas {
    position: relative;
    width: 1200px;
    height: 843px;
  }
  .cover {
    position: absolute;
    left: 352px;
    top: 67px;
    width: 496px;
    height: 704px;
    background: var(--paper);
    overflow: hidden;
  }
  .cover__kicker {
    position: absolute;
    top: 30px;
    left: 0;
    width: 100%;
    text-align: center;
    font-family: "Oswald", sans-serif;
    font-weight: 400;
    font-size: 44px;
    line-height: 1;
    letter-spacing: 2px;
    color: var(--ink);
  }
  .title-panel {
    position: absolute;
    left: 25px;
    top: 87px;
    width: 447px;
    height: 223px;
    background: var(--title-panel);
    border: 8px solid var(--accent-red);
    display: flex;
    flex-direction: column;
    justify-content: center;
    align-items: center;
  }
  .title-panel__line {
    font-family: "Oswald", sans-serif;
    font-weight: 500;
    font-size: 88px;
    line-height: 1.02;
    letter-spacing: 1px;
    color: var(--white);
    white-space: nowrap;
  }
  .cover__subtitle {
    position: absolute;
    top: 320px;
    left: 0;
    width: 100%;
    text-align: center;
    font-family: "Montserrat", sans-serif;
    font-weight: 500;
    font-size: 18px;
    letter-spacing: 3px;
    color: var(--ink);
    white-space: nowrap;
  }
  .pillar {
    position: absolute;
    background: linear-gradient(90deg, var(--stone-dark) 0%, var(--stone-light) 30%, var(--stone-mid) 55%, var(--stone-light) 78%, var(--stone-dark) 100%);
    border-radius: 4px 4px 0 0;
  }
  .pillar--left  { left: 67px;  top: 420px; width: 107px; height: 229px; }
  .pillar--front { left: 181px; top: 355px; width: 120px; height: 294px; }
  .pillar--right { left: 327px; top: 420px; width: 109px; height: 229px; }
  .author-band {
    position: absolute;
    left: 0;
    top: 652px;
    width: 100%;
    height: 42px;
    background: var(--accent-red);
    display: flex;
    align-items: center;
    justify-content: center;
  }
  .author-band__name {
    font-family: "Montserrat", sans-serif;
    font-weight: 600;
    font-size: 22px;
    letter-spacing: 6px;
    color: var(--white);
  }
</style>
</head>
<body>
  <main class="canvas">
    <article class="cover">
      <p class="cover__kicker">BUILDING</p>
      <h1 class="title-panel">
        <span class="title-panel__line">SENTENCES</span>
        <span class="title-panel__line">THAT STICK</span>
      </h1>
      <p class="cover__subtitle">A FRIENDLY PATH THROUGH USAGE</p>
      <div class="pillar pillar--left" role="img" aria-label="White Ionic stone pillar, left, set back"></div>
      <div class="pillar pillar--front" role="img" aria-label="Taller white Ionic stone pillar standing in front, centre"></div>
      <div class="pillar pillar--right" role="img" aria-label="White Ionic stone pillar, right, set back"></div>
      <footer class="author-band">
        <span class="author-band__name">DOREEN CALLOWAY</span>
      </footer>
    </article>
  </main>
</body>
</html>
```